Varnik Holdings — Business Card Design Brief
Overview
Design a double-sided business card for Varnik Holdings that highlights our two service arms: Varnik Communications (telecommunications) and Varnik Energy (business energy solutions). The card should feel smart and stand out when handed to clients.

Objectives
Showcase our areas of specialty clearly.
Reflect the overall Varnik / Varnik Holdings brand while acknowledging both arms.
Explore using both logos (Communications + Energy) or one unified logo, depending on the design.

Deliverables
One double-sided business card design (front + back).

Content & Copy
Front (preferred): Logo: Varnik / Varnik Holdings
Descriptor: Business Communications | Business Energy
Back:My contact details and company details
Core products: Business Mobile • Telephony • Internet • Business Energy Solutions

Brand & Visual Direction
We have a group logo currently tailored more toward telecoms, plus a separate Varnik Energy logo.
Please explore layouts that use both logos or just one, whichever works best.
Color: I wouldn't mind seeing an option using our the Blue/Purple gradient from our website (varnik-example.co.uk), but also open to non-gradient approaches and other colours..

Overall look: Smart, modern, and distinctive.
Format & Print Specs
Double-sided business card format. (Use a standard size

Must-Haves
Front: Varnik wording or Varnik Holdings wording with atleast 1 logo also on front “Business Communications | Business Energy.”

Back: Contact + company details and core products.
A design that stands out while remaining professional.

Nice-to-Have Options
A gradient version using our site’s Blue/Purple gradient.
A non-gradient version.
A dual-logo treatment versus a single-logo treatment.

Thanks
Owen

```html
<!DOCTYPE html>
<html lang="en">
<head>
<meta charset="utf-8">
<title>Varnik Holdings – Business Card</title>
<link rel="stylesheet" href="https://fonts.googleapis.com/css2?family=Montserrat:wght@400;600;700;800&family=Poppins:wght@700&family=Roboto+Condensed:wght@700&display=swap">
<style>
  :root {
    --stage: #9a9a9a;
    --card: #ffffff;
    --navy: #1c1565;
    --ink: #222222;
    --heading: #333333;
    --green: #4cae2a;
    --blue: #1f6fdc;
    --divider: #555555;
  }
  html, body {
    margin: 0;
    padding: 0;
    width: 1200px;
    height: 1059px;
    overflow: hidden;
    background: var(--stage);
  }
  .canvas {
    position: relative;
    width: 1200px;
    height: 1059px;
  }
  .card {
    position: absolute;
    background: var(--card);
    border-radius: 26px;
    overflow: hidden;
  }
  .card--front { left: 252px; top: 88px; width: 724px; height: 415px; }
  .card--back  { left: 252px; top: 566px; width: 712px; height: 407px; }

  .brand-mark {
    position: absolute;
    border-radius: 50%;
  }
  .card--front .brand-mark {
    left: 316px; top: 40px; width: 92px; height: 92px;
    background: var(--green);
  }
  .card--back .brand-mark {
    left: 296px; top: 162px; width: 116px; height: 116px;
    background: var(--blue);
  }
  .brand-name {
    position: absolute;
    left: 0; right: 0;
    text-align: center;
    margin: 0;
    font-family: "Montserrat", sans-serif;
    font-weight: 800;
    color: var(--navy);
    letter-spacing: 1px;
    line-height: 1;
  }
  .card--front .brand-name { top: 140px; font-size: 52px; }
  .card--back .brand-name  { top: 290px; font-size: 54px; }

  .descriptor {
    position: absolute;
    left: 0; right: 0; top: 356px;
    margin: 0;
    text-align: center;
    font-family: "Montserrat", sans-serif;
    font-weight: 600;
    font-size: 15px;
    letter-spacing: 0.5px;
    color: var(--heading);
  }

  .person {
    position: absolute;
    right: 385px;
    top: 236px;
    text-align: right;
    font-family: "Montserrat", sans-serif;
  }
  .person__name {
    margin: 0;
    font-size: 28px;
    font-weight: 700;
    color: var(--navy);
    line-height: 1.1;
  }
  .person__role {
    margin: 2px 0 0;
    font-size: 20px;
    font-weight: 400;
    color: var(--ink);
    letter-spacing: 0.5px;
    line-height: 1.1;
  }
  .divider {
    position: absolute;
    left: 368px; top: 227px;
    width: 1.5px; height: 92px;
    background: var(--divider);
  }
  .contacts {
    position: absolute;
    left: 382px; top: 224px;
    margin: 0; padding: 0;
    list-style: none;
    font-family: "Montserrat", sans-serif;
    font-size: 20px;
    color: var(--ink);
  }
  .contacts li {
    display: flex;
    align-items: center;
    height: 33.5px;
  }
  .contacts svg {
    width: 18px; height: 18px;
    margin-right: 12px;
    flex: none;
  }
  .services {
    position: absolute;
    left: 0; right: 0;
    top: 340px; height: 42px;
    background: var(--navy);
    color: #ffffff;
    font-family: "Roboto Condensed", sans-serif;
    font-weight: 700;
    font-size: 24px;
    line-height: 42px;
    padding-left: 18px;
    white-space: nowrap;
    word-spacing: 1px;
  }
  .group-title {
    position: absolute;
    left: 0; right: 0; top: 70px;
    margin: 0;
    text-align: center;
    font-family: "Poppins", sans-serif;
    font-weight: 700;
    font-size: 50px;
    color: var(--heading);
    line-height: 1;
  }
</style>
</head>
<body>
<main class="canvas">
  <section class="card card--front" aria-label="Card front">
    <span class="brand-mark" aria-hidden="true"></span>
    <p class="brand-name">VARNIK</p>

    <div class="person">
      <p class="person__name">Mira Castell</p>
      <p class="person__role">Owner</p>
    </div>
    <span class="divider" aria-hidden="true"></span>

    <ul class="contacts">
      <li>
        <svg viewBox="0 0 24 24" aria-hidden="true"><path fill="#4cae2a" d="M6.6 10.8a15.1 15.1 0 0 0 6.6 6.6l2.2-2.2c.3-.3.7-.4 1-.2 1.1.4 2.3.6 3.6.6.6 0 1 .4 1 1V20c0 .6-.4 1-1 1C10.6 21 3 13.4 3 4c0-.6.4-1 1-1h3.5c.6 0 1 .4 1 1 0 1.3.2 2.5.6 3.6.1.3 0 .7-.2 1z"/></svg>
        044-000 555 014
      </li>
      <li>
        <svg viewBox="0 0 24 24" aria-hidden="true"><rect x="2" y="5" width="20" height="14" rx="1" fill="#4cae2a"/><path d="M2.5 6l9.5 7 9.5-7" fill="none" stroke="#fff" stroke-width="1.8"/></svg>
        hello@varnik-example.co.uk
      </li>
      <li>
        <svg viewBox="0 0 24 24" aria-hidden="true"><circle cx="12" cy="12" r="10" fill="none" stroke="#4cae2a" stroke-width="2"/><path d="M2 12h20M12 2c3 3 3 17 0 20M12 2c-3 3-3 17 0 20" fill="none" stroke="#4cae2a" stroke-width="1.6"/></svg>
        www.varnik-example.co.uk
      </li>
    </ul>

    <div class="services">• Business Mobile &nbsp;• Telephony &nbsp;• Internet &nbsp;• Business Energy Solutions</div>
  </section>

  <section class="card card--back" aria-label="Card back">
    <h1 class="group-title">Varnik Holdings</h1>
    <span class="brand-mark" aria-hidden="true"></span>
    <p class="brand-name">VARNIK</p>
    <p class="descriptor">Business Communications | Business Energy</p>
  </section>
</main>
</body>
</html>
```